New Business Card Design Project

Use the flyer uploaded and website www.brightoakbuilders.com for inspiration.
List Our Services on Backside of business cards
Marcus Delling
Harborline Builders Inc.
Licensed General Contractors
858-471-6093

Contact Information for Business Card

Use the flyer uploaded and website www.brightoakbuilders.com for inspiration. List Our Services on Backside of business cards Marcus Delling Harborline Builders Inc. Licensed General Contractors 858-471-6093

```html
<!DOCTYPE html>
<html lang="en">
<head>
<meta charset="utf-8">
<title>Harborline Builders – Business Card</title>
<link rel="stylesheet" href="https://fonts.googleapis.com/css2?family=Cinzel:wght@400&family=Montserrat:wght@400;500;700;800&display=swap">
<style>
  :root {
    --page-bg: #e9e8e6;
    --card-white: #ffffff;
    --card-dark: #222223;
    --ink: #111111;
    --ink-soft: #333333;
    --on-dark: #f2f2f2;
    --accent-blue: #2f7fd6;
    --rule: #222222;
  }
  * { box-sizing: border-box; margin: 0; padding: 0; }
  html, body { width: 1200px; height: 786px; overflow: hidden; }
  body {
    background: var(--page-bg);
    font-family: "Montserrat", Arial, sans-serif;
    position: relative;
  }
  .card {
    position: absolute;
    top: 238px;
    width: 540px;
    height: 310px;
    box-shadow: 0 4px 14px rgba(0,0,0,0.18);
  }
  /* Front */
  .card-front { left: 40px; background: var(--card-white); color: var(--ink); }
  .front-brand {
    position: absolute; left: 36px; top: 52px;
    font-family: "Cinzel", Georgia, serif;
    font-size: 25px; letter-spacing: 1px; color: var(--ink);
  }
  .front-brand-mark {
    display: inline-block; width: 10px; height: 10px;
    background: var(--ink); margin-left: 10px; vertical-align: middle;
  }
  .holder { position: absolute; left: 36px; top: 150px; width: 240px; }
  .holder-name { font-weight: 800; font-size: 20px; line-height: 1.1; }
  .holder-title { font-size: 12px; color: var(--ink-soft); margin-top: 2px; }
  .holder-rule { border-top: 1px solid var(--rule); margin: 8px 0; }
  .licence { font-size: 12px; font-weight: 500; }
  .contact-list { list-style: none; }
  .contact-item {
    display: flex; align-items: center; gap: 9px;
    font-size: 12.5px; font-weight: 500; line-height: 20px;
  }
  .contact-icon { width: 11px; height: 11px; flex: none; }
  /* Back */
  .card-back { left: 620px; background: var(--card-dark); color: var(--on-dark); }
  .back-brand {
    position: absolute; left: 30px; top: 138px; width: 230px; text-align: center;
    font-family: "Cinzel", Georgia, serif;
    font-size: 21px; letter-spacing: 1px; color: var(--on-dark);
  }
  .back-divider {
    position: absolute; left: 282px; top: 56px; width: 1.5px; height: 196px;
    background: var(--accent-blue);
  }
  .services { position: absolute; left: 300px; top: 62px; }
  .services-title { color: var(--accent-blue); font-weight: 700; font-size: 15px; margin-bottom: 4px; }
  .services-list { list-style: none; }
  .service {
    font-size: 11px; line-height: 15.5px; color: var(--on-dark);
    position: relative; padding-left: 12px;
  }
  .service::before {
    content: ""; position: absolute; left: 0; top: 6px;
    width: 4px; height: 4px; border-radius: 50%; background: var(--accent-blue);
  }
</style>
</head>
<body>
  <section class="card card-front">
    <div class="front-brand">Harborline Builders<span class="front-brand-mark"></span></div>
    <div class="holder">
      <h1 class="holder-name">Marcus Delling</h1>
      <p class="holder-title">Managing Director</p>
      <div class="holder-rule"></div>
      <p class="licence">CSLB&nbsp; Licensed no #1048275</p>
      <div class="holder-rule"></div>
      <ul class="contact-list">
        <li class="contact-item">
          <svg class="contact-icon" viewBox="0 0 12 12"><path d="M1 4 Q6 0 11 4 L9 5.5 L7.5 4 L4.5 4 L3 5.5 Z M3 6.5 H9 L10 11 H2 Z" fill="#111"/></svg>
          858-471-6093
        </li>
        <li class="contact-item">
          <svg class="contact-icon" viewBox="0 0 12 12"><rect x="0.5" y="2" width="11" height="8" fill="#111"/><path d="M0.5 2 L6 6.5 L11.5 2" stroke="#fff" stroke-width="1" fill="none"/></svg>
          info@brightoakbuilders.com
        </li>
        <li class="contact-item">
          <svg class="contact-icon" viewBox="0 0 12 12"><circle cx="6" cy="6" r="5.5" fill="#111"/><path d="M0.5 6 H11.5 M6 0.5 C3 3 3 9 6 11.5 C9 9 9 3 6 0.5" stroke="#fff" stroke-width="0.8" fill="none"/></svg>
          brightoakbuilders.com
        </li>
      </ul>
    </div>
  </section>

  <section class="card card-back">
    <div class="back-brand">Harborline Builders</div>
    <div class="back-divider"></div>
    <div class="services">
      <h2 class="services-title">Our Services</h2>
      <ul class="services-list">
        <li class="service">Remodel: Kitchen &amp; Bath</li>
        <li class="service">Painting: Interior &amp; Exterior</li>
        <li class="service">Flooring: Carpet, Vinyl, Wood</li>
        <li class="service">Window &amp; Door Replacement</li>
        <li class="service">Plumbing Repair &amp; Upgrades</li>
        <li class="service">Energy Efficient Upgrades</li>
        <li class="service">Deck &amp; Patio construction</li>
        <li class="service">Water &amp; Mold Damage</li>
        <li class="service">Garage Renovation</li>
      </ul>
    </div>
  </section>
</body>
</html>
```